The book is called "Distance Racing Blueprints: An In-Depth Manual for Achieving Your Peak Race Day - Featuring Schedules, Counsel and Target-Reaching Pointers "

It is a 6" x 9" book with 205 pages. This is an advanced book for runners who have been running and trying to hit their marathon goals, but haven't been able to do so. This needs to portray a professional coaching image and high performing athlete.

I have running photos of myself running marathons if you thought that was the route to take, but I'm open to your creative influence.

```html
<!DOCTYPE html>
<html lang="en">
<head>
<meta charset="utf-8">
<title>Distance Racing Blueprints – Cover Wrap</title>
<link href="https://fonts.googleapis.com/css2?family=Inter:ital,wght@0,400;0,700;0,800;1,400;1,700&display=swap" rel="stylesheet">
<style>
  :root {
    --stage: #2b2b2b;
    --paper: #ffffff;
    --red: #f01e00;
    --grey: #a3a19f;
    --ink: #0a0a0a;
    --photo-light: #f1f0ee;
    --photo-mid: #d9d5cf;
  }
  * { box-sizing: border-box; margin: 0; padding: 0; }
  html, body {
    width: 1200px; height: 1200px; overflow: hidden;
    background: var(--stage);
    font-family: "Inter", Arial, sans-serif;
    color: var(--ink);
  }
  .cover-wrap {
    position: absolute; left: 40px; top: 204px;
    width: 1120px; height: 792px;
    background: var(--paper);
  }
  .panel { position: absolute; top: 0; height: 100%; }
  .back-cover { left: 0; width: 535px; }
  .spine { left: 535px; width: 45px; }
  .front-cover { left: 580px; width: 540px; }

  .title { font-weight: 700; letter-spacing: -0.045em; }
  .title .line-red { color: var(--red); display: block; }
  .title .line-grey { color: var(--grey); display: block; }
  .title .line-black { color: var(--ink); display: block; }

  /* back */
  .back-title {
    position: absolute; left: 48px; top: 46px;
    font-size: 38px; line-height: 31px; text-align: center; width: 200px;
  }
  .back-subtitle {
    position: absolute; right: 56px; top: 74px; width: 230px;
    text-align: right; font-size: 13.6px; line-height: 19.5px;
  }
  .back-subtitle b { font-weight: 700; }
  .back-blurb {
    position: absolute; left: 49px; top: 168px; width: 430px;
    font-size: 13.2px; line-height: 18.3px; text-align: justify;
  }
  .photo {
    position: absolute;
    background: radial-gradient(ellipse at 50% 55%, var(--photo-mid) 0%, var(--photo-light) 55%, var(--paper) 80%);
  }
  .back-photo { left: 26px; top: 468px; width: 488px; height: 236px; }

  /* spine */
  .spine-title, .spine-author {
    position: absolute; left: 50%; transform: translateX(-50%);
    writing-mode: vertical-rl; white-space: nowrap;
  }
  .spine-title { top: 54px; font-size: 27px; }
  .spine-author { top: 606px; font-size: 22px; font-weight: 700; letter-spacing: -0.02em; }

  /* front */
  .badge {
    position: absolute; left: 364px; top: 27px; width: 150px; height: 150px;
    transform: rotate(-12deg);
  }
  .badge svg { position: absolute; inset: 0; }
  .badge-text {
    position: absolute; inset: 0;
    display: flex; flex-direction: column; justify-content: center; align-items: center;
    color: var(--paper); font-size: 10.5px; line-height: 11.6px; text-align: center;
  }
  .badge-text b { font-weight: 800; }
  .front-title {
    position: absolute; left: 0; top: 186px; width: 100%;
    font-size: 92px; line-height: 74px; text-align: center;
  }
  .front-title .line-grey { padding-left: 40px; }
  .front-photo { left: 24px; top: 475px; width: 495px; height: 230px; }
  .front-author {
    position: absolute; left: 51px; top: 726px;
    font-size: 28px; font-weight: 700; letter-spacing: -0.01em;
  }
</style>
</head>
<body>
<main class="cover-wrap">

  <section class="panel back-cover">
    <h2 class="title back-title">
      <span class="line-red">Distance</span>
      <span class="line-grey">Racing</span>
      <span class="line-black">Blueprints</span>
    </h2>
    <p class="back-subtitle">
      <b>An In-Depth Manual</b> for<br>
      <i>Achieving Your Peak Race Day</i><br>
      <b>Featuring Schedules, Counsel and<br>Target-Reaching Pointers</b>
    </p>
    <p class="back-blurb">Lorem ipsum dolor sit amet, consectetur adipiscing elit, sed do eiusmod tempor incididunt ut labore et dolore magna aliqua. Quis ipsum suspendisse ultrices gravida. Risus commodo viverra maecenas accumsan lacus vel facilisis. Lorem ipsum dolor sit amet, consectetur adipiscing elit, sed do eiusmod tempor incididunt ut labore et dolore magna aliqua. Quis ipsum suspendisse ultrices gravida. Risus commodo viverra maecenas accumsan lacus vel facilisis. Lorem ipsum dolor sit amet, consectetur adipiscing elit, sed do eiusmod tempor incididunt ut labore et dolore magna aliqua. Quis ipsum suspendisse ultrices gravida. Risus commodo viverra maecenas accumsan lacus vel facilisis. Lorem ipsum dolor sit amet, consectetur adipiscing elit, sed do eiusmod tempor incididunt ut labore et dolore magna aliqua. Quis ipsum suspendisse ultrices gravida. Risus commodo viverra maecenas accumsan lacus vel facilisis.</p>
    <div class="photo back-photo" role="img" aria-label="Photo of four runners in sportswear running side by side, cut out on white"></div>
  </section>

  <section class="panel spine">
    <p class="title spine-title"><span style="color:var(--red)">Distance</span> <span style="color:var(--grey)">Racing</span> <span style="color:var(--ink)">Blueprints</span></p>
    <p class="spine-author">Author Name</p>
  </section>

  <section class="panel front-cover">
    <div class="badge">
      <svg viewBox="0 0 150 150" width="150" height="150" aria-hidden="true">
        <polygon fill="var(--red)" points="150,75 137.8,87.5 144.3,103.7 128.2,110.6 128,128 110.6,128.2 103.7,144.3 87.5,137.8 75,150 62.5,137.8 46.3,144.3 39.4,128.2 22,128 21.8,110.6 5.7,103.7 12.2,87.5 0,75 12.2,62.5 5.7,46.3 21.8,39.4 22,22 39.4,21.8 46.3,5.7 62.5,12.2 75,0 87.5,12.2 103.7,5.7 110.6,21.8 128,22 128.2,39.4 144.3,46.3 137.8,62.5"/>
      </svg>
      <p class="badge-text">
        <b>An In-Depth</b>
        <b>Manual</b> for
        <i>Achieving Your</i>
        <i>Peak Race Day</i>
        <b>Featuring Schedules,</b>
        <b>Counsel and</b>
        <b>Target-Reaching</b>
        <b>Pointers</b>
      </p>
    </div>
    <h1 class="title front-title">
      <span class="line-red">Distance</span>
      <span class="line-grey">Racing</span>
      <span class="line-black">Blueprints</span>
    </h1>
    <div class="photo front-photo" role="img" aria-label="Photo of four athletes running in stride in colourful training tops, cut out on white"></div>
    <p class="front-author">Author Name</p>
  </section>

</main>
</body>
</html>
```